Business Card for a New Zealand IT Startup

I need a business card for VELTA Holdings. We are a young startup based in New Zealand working in internet marketing and web development. The design should have some element connected to New Zealand, such as wave, koru or silver fern, just don't use a kiwi bird.

```html
<!DOCTYPE html>
<html lang="en">
<head>
<meta charset="utf-8">
<title>VELTA Holdings – Business Card</title>
<link rel="stylesheet" href="https://fonts.googleapis.com/css2?family=Montserrat:wght@600;700&family=Didact+Gothic&display=swap">
<style>
  :root {
    --backdrop: #2b2b2b;
    --brand-blue: #0a6fbd;
    --brand-orange: #f15a22;
    --card-white: #ffffff;
    --ink: #3a3a3a;
    --rule: #8a8a8a;
  }
  * { box-sizing: border-box; margin: 0; padding: 0; }
  html, body { width: 1200px; height: 768px; overflow: hidden; }
  body {
    background: var(--backdrop);
    font-family: "Didact Gothic", "Century Gothic", sans-serif;
    position: relative;
  }
  .card {
    position: absolute;
    top: 222px;
    width: 540px;
    height: 324px;
    border-radius: 22px;
    overflow: hidden;
  }
  /* Reverse side */
  .card--back {
    left: 40px;
    background: var(--brand-blue);
    color: var(--card-white);
  }
  .back-brand {
    position: absolute;
    top: 118px; left: 0; right: 0;
    display: flex; align-items: center; justify-content: center; gap: 14px;
  }
  .back-brand__dot {
    width: 40px; height: 40px; border-radius: 50%;
    background: var(--card-white);
  }
  .back-brand__name {
    font-family: "Montserrat", sans-serif;
    font-weight: 700;
    font-size: 34px;
    color: var(--card-white);
  }
  .back-web {
    position: absolute;
    bottom: 40px; left: 0; right: 0;
    text-align: center;
    font-size: 13px;
    letter-spacing: 5px;
  }
  /* Front side */
  .card--front {
    left: 620px;
    background: var(--card-white);
    color: var(--ink);
  }
  .front-brand {
    position: absolute;
    top: 44px; right: 34px;
    font-family: "Montserrat", sans-serif;
    font-weight: 700;
    font-size: 28px;
    line-height: 1.1;
    color: var(--brand-blue);
  }
  .person {
    position: absolute;
    top: 66px; left: 30px;
  }
  .person__name {
    font-family: "Montserrat", sans-serif;
    font-weight: 700;
    font-size: 21px;
    color: var(--brand-blue);
    line-height: 1;
  }
  .person__role {
    font-size: 14px;
    color: var(--brand-orange);
    margin-top: 3px;
  }
  .divider {
    position: absolute;
    top: 112px; left: 30px; right: 30px;
    height: 1px;
    background: var(--rule);
  }
  .contacts {
    position: absolute;
    top: 124px; left: 30px;
    list-style: none;
    font-size: 14px;
    line-height: 21px;
  }
  .contacts li { display: flex; align-items: center; gap: 8px; }
  .contacts svg { width: 13px; height: 13px; fill: var(--brand-blue); flex: none; }
  .address {
    position: absolute;
    right: 34px; bottom: 42px;
    text-align: right;
    font-size: 15px;
    line-height: 20px;
  }
  .edge-band {
    position: absolute;
    left: 0; right: 0; bottom: 0;
    height: 18px;
  }
</style>
</head>
<body>

<section class="card card--back" aria-label="Card reverse">
  <div class="back-brand">
    <span class="back-brand__dot"></span>
    <span class="back-brand__name">VELTA Holdings</span>
  </div>
  <p class="back-web">www.veltaholdings.com</p>
</section>

<section class="card card--front" aria-label="Card front">
  <div class="front-brand">VELTA Holdings</div>

  <div class="person">
    <p class="person__name">MARA QUINLAN</p>
    <p class="person__role">CEO/FOUNDER</p>
  </div>

  <div class="divider"></div>

  <ul class="contacts">
    <li>
      <svg viewBox="0 0 24 24" aria-hidden="true"><path d="M6.6 10.8a15 15 0 0 0 6.6 6.6l2.2-2.2c.3-.3.7-.4 1-.2 1.1.4 2.3.6 3.6.6.6 0 1 .4 1 1V20c0 .6-.4 1-1 1C10.6 21 3 13.4 3 4c0-.6.4-1 1-1h3.5c.6 0 1 .4 1 1 0 1.3.2 2.5.6 3.6.1.3 0 .7-.2 1z"/></svg>
      021 583 7146
    </li>
    <li>
      <svg viewBox="0 0 24 24" aria-hidden="true"><path d="M7 1h10a2 2 0 0 1 2 2v18a2 2 0 0 1-2 2H7a2 2 0 0 1-2-2V3a2 2 0 0 1 2-2zm0 3v14h10V4z"/></svg>
      027 219 4805
    </li>
    <li>
      <svg viewBox="0 0 24 24" aria-hidden="true"><path d="M6 2h12v6H6zM3 9h18a1 1 0 0 1 1 1v8h-4v4H6v-4H2v-8a1 1 0 0 1 1-1zm5 7v4h8v-4z"/></svg>
      04 762 3091
    </li>
    <li>
      <svg viewBox="0 0 24 24" aria-hidden="true"><path d="M2 5h20v14H2zm2 2v.5l8 5 8-5V7z"/></svg>
      mara@veltaholdings.com
    </li>
  </ul>

  <p class="address">1420 Harbour View Road<br>Wellington, New Zealand 6011<br>www.veltaholdings.com</p>

  <svg class="edge-band" viewBox="0 0 540 18" preserveAspectRatio="none" aria-hidden="true">
    <polygon points="0,0 292,0 286,18 0,18" fill="var(--brand-blue)"/>
    <polygon points="298,0 540,0 540,18 292,18" fill="var(--brand-orange)"/>
  </svg>
</section>

</body>
</html>
```